International Travel & Visas Firm needs a Schengen Visa eBook Cover Design

We need an ebook cover design for an online based travel, immigration, visas & nationality law firm called 'OrV' (orbit and voyage). We are all about helping people overcome the obstacles to travel and ensuring that people achieve their dreams and ambitions through travel to various destinations and bettering their lives.This initial ebook cover is for our downloaded pdf ebook all about Schengen visas and travelling to any of the 26 European countries that form the Schengen Zone.We want people to be excited about buying this book even before receiving it.We would like to see amazing designs that also speak to our logo and new branding.Check out https://orbitandvoyage.example/schengen-visas/ and http://orbitandvoyage.pages.funnelbox.example/start-your-schengen-visa-application

Target Market(s)

Travellers that want to get a visa to travel around Europe

Industry/Entity Type

Travel Industry

Colors
fbee3d
faa54b

Requirements
Must have
• - Title:
• Schengen Visa Guide
Nice to have
• - tagline:
• Liberate yourself and travel to 26 European Countries
• - OrV Logo
• - Reference to it being an insider's guide to Schengen Visas
• - a play on the word OrV (I am)

```html
<!DOCTYPE html>
<html lang="en">
<head>
<meta charset="utf-8">
<title>Schengen Visa Guide – eBook Cover</title>
<link rel="stylesheet" href="https://fonts.googleapis.com/css2?family=Bebas+Neue&family=Mulish:wght@400;600&display=swap">
<style>
  :root {
    --stage: #e6e5e4;
    --navy: #1a2d48;
    --orange: #fb5a1e;
    --gold: #f3b61b;
    --white: #ffffff;
    --rule: #8a97ab;
    --art-teal: #5cc4cf;
    --art-sky: #a9dff0;
  }
  * { margin: 0; padding: 0; box-sizing: border-box; }
  html, body {
    width: 1200px;
    height: 1200px;
    overflow: hidden;
    background: var(--stage);
  }
  .cover {
    position: absolute;
    left: 231px;
    top: 50px;
    width: 738px;
    height: 1100px;
    background: var(--navy);
    overflow: hidden;
    box-shadow: 0 10px 30px rgba(0,0,0,.18);
  }
  .brand {
    position: absolute;
    top: 34px;
    left: 0;
    width: 100%;
    text-align: center;
    color: var(--white);
    font-family: "Mulish", sans-serif;
  }
  .brand-name {
    display: block;
    font-size: 66px;
    font-weight: 600;
    line-height: 72px;
    letter-spacing: 1px;
  }
  .brand-sub {
    display: block;
    margin-top: 2px;
    font-size: 12px;
    font-weight: 600;
    letter-spacing: .4px;
  }
  .title {
    position: absolute;
    left: 0;
    width: 100%;
    text-align: center;
    font-family: "Bebas Neue", sans-serif;
    font-weight: 400;
  }
  .title-top {
    top: 148px;
    color: var(--orange);
    font-size: 118px;
    line-height: 118px;
    letter-spacing: 0;
  }
  .title-main {
    top: 240px;
    color: var(--gold);
    font-size: 312px;
    line-height: 300px;
    letter-spacing: 2px;
  }
  .rule {
    position: absolute;
    left: 100px;
    width: 518px;
    height: 2px;
    background: linear-gradient(90deg, transparent, var(--rule) 20%, var(--rule) 80%, transparent);
  }
  .rule-top { top: 502px; }
  .rule-bottom { top: 587px; }
  .tagline {
    position: absolute;
    top: 518px;
    left: 0;
    width: 100%;
    text-align: center;
    color: var(--white);
    font-family: "Mulish", sans-serif;
    font-size: 22px;
    font-weight: 400;
    line-height: 30px;
    text-transform: uppercase;
  }
  .travel-art {
    position: absolute;
    left: 72px;
    top: 619px;
    width: 590px;
    height: 440px;
    border-radius: 40% 40% 8px 8px;
    background:
      radial-gradient(ellipse at 60% 45%, var(--art-teal) 0%, transparent 55%),
      radial-gradient(ellipse at 45% 80%, var(--gold) 0%, transparent 50%),
      radial-gradient(ellipse at 80% 55%, var(--art-sky) 0%, transparent 50%),
      radial-gradient(ellipse at 25% 55%, #c94a3a 0%, transparent 45%);
    opacity: .85;
  }
  .footer-band {
    position: absolute;
    left: 0;
    bottom: 0;
    width: 100%;
    height: 52px;
    background: var(--gold);
  }
</style>
</head>
<body>
  <main class="cover">
    <header class="brand">
      <span class="brand-name">OrV</span>
      <span class="brand-sub">orbit and voyage</span>
    </header>

    <h1>
      <span class="title title-top">Schengen Visa</span>
      <span class="title title-main">Guide</span>
    </h1>

    <div class="rule rule-top"></div>
    <p class="tagline">Liberate yourself and travel to 26<br>European countries</p>
    <div class="rule rule-bottom"></div>

    <div class="travel-art" role="img" aria-label="Travel illustration: world landmarks, hot air balloon, airplane, passport, boarding pass, camera, yellow taxi and sun hat"></div>

    <div class="footer-band"></div>
  </main>
</body>
</html>
```